Need Website Design for Non-Profit Veteran Site

I am looking for a very talented creative website designer for a modern feel. I'll give a little bit of guidance around what I am looking for and then your creative juices should kick in and design away. I have already purchased the domain but will need hosting (at least temporarily) and the creative design work done.The website domain is militarydocs.orgI am looking to attract current and veteran military providers (doctors, nurse practitioners, physician assistants, etc) to join and signup for membership. They would pay a yearly fee to join. Would need membership categories $135 for Provider, $55 Student, $100 for Retired, and Organization (Organization would be broken down into Less than 100 ($200), 100-249 ($250), 250-499 ($300), 500-999 ($400), 1,000-2,999 ($500), and 3,000 ($700). Would need Benefit built out and would need to accept money through CoinVane and other means. Since it's a new organization just starting, would also need a Donate button to get people to donate if they want any amount they would like. The second part of the website is that once they join, they will have acess to a list of all other providers who have registered within the website (not exportable) so they can connect with one another. If they want to see contact information this will be included in their fee as a benefit to socialize with one another. As part of the website, there will be another Veteran's portal so veterans who would like to connect with a provider around a particular speciality can reach out and request help from the doctor writing a nexus letter or letter to support the veteran who is filing a claim with the BQ. Veterans would pay a yearly sign-up fee of $30.00 and would need their membership benefits displayed. They would have access to a list of veterans in their region by state and distance, and can reach out to doctors to get their help. If a doctor and veteran agree, sharable inforamtion of medical hipaa documents can be exchanged via the website. The physician and veteran can negotiate a fee through the website only and share their details. This is a separate fee for this type of process between the provider and veteran. We will collect a $250 fee for admin on each of these and each project the veteran does with the provider will cost $450 (so essentially the doctor gets paid $450 and i get $250.00. This model could be changed over time as we start to test this out). A good example of 50% of what I'm looking for is something like the following website: https://www.lpkt.org/ It has some of the features but not all and my site should be more modernized to attract the veteran and military providers.

Target Market(s)

Current and retired military providers and veterans

Industry/Entity Type

Non Profit

Number of Pages Required

1 page

Requirements
Must have
• Military Design
• Modern Feel (Example templates for feel -https://quillmoth.com/free-photoshop-psd-web-design-template/)
• Donation box
• Stuff mentioned in the description)
Nice to have
• Open to feedback
Should not have
• Open to feedback

```html
<!DOCTYPE html>
<html lang="en">
<head>
<meta charset="utf-8">
<title>Harborwell</title>
<link href="https://fonts.googleapis.com/css2?family=Lora:wght@400;700&family=Open+Sans:wght@400;600&display=swap" rel="stylesheet">
<style>
:root{
  --olive:#5d6a35;
  --olive-dark:#4a5629;
  --olive-deep:#2f3820;
  --camo:#6f7b45;
  --ink:#111;
  --paper:#fff;
  --footer:#2b2b2b;
  --footer-bottom:#1a1a1a;
  --accent-red:#d2281e;
  --muted:#ddd;
}
*{box-sizing:border-box;margin:0;padding:0}
html,body{width:667px;height:1200px;overflow:hidden;background:var(--paper)}
body{font-family:"Open Sans",sans-serif;color:var(--ink);position:relative}

/* Header */
.site-header{position:absolute;top:0;left:0;width:667px;height:75px;background:var(--paper)}
.brand{position:absolute;left:55px;top:12px;font-family:"Lora",serif;font-size:22px;color:var(--olive);letter-spacing:.5px}
.header-actions{position:absolute;top:12px;right:54px;display:flex;gap:8px}
.btn-sm{font-family:"Lora",serif;font-size:7.5px;font-weight:700;padding:0 10px;height:19px;line-height:17px;border-radius:3px;border:1px solid var(--olive);background:var(--olive);color:var(--paper);text-transform:uppercase}
.btn-sm.outline{background:var(--paper);color:var(--olive)}
.main-nav{position:absolute;top:47px;right:54px;display:flex;gap:23px;font-family:"Lora",serif;font-size:9.5px;font-weight:700;color:#222}
.main-nav .active{color:var(--olive)}

/* Hero */
.hero{position:absolute;top:75px;left:0;width:667px;height:263px;overflow:hidden}
.hero-photo{position:absolute;inset:0;background:linear-gradient(90deg,#e9ebe8 0%,#dfe3e2 40%,#c9d1d6 65%,#a58b6a 90%,#8f7555 100%)}
.hero-title{position:absolute;left:68px;top:70px;font-family:"Lora",serif;font-weight:700;font-size:40px;color:#0d0d0d}
.hero-sub{position:absolute;left:58px;top:121px;width:280px;text-align:center;font-family:"Lora",serif;font-size:16px;line-height:21px;color:#333}
.btn-donate{position:absolute;left:148px;top:173px;width:95px;height:26px;border-radius:3px;background:var(--olive);color:var(--paper);font-family:"Lora",serif;font-weight:700;font-size:9px;text-align:center;line-height:26px}
.hero-dots{position:absolute;left:313px;top:239px;display:flex;gap:3px}
.hero-dots span{width:8px;height:8px;border-radius:50%;border:1px solid #111;background:var(--paper)}
.hero-dots span.on{background:#111}

/* About */
.about{position:absolute;top:338px;left:0;width:667px;height:215px;background:linear-gradient(135deg,#5f6b3a,#57632f 60%,#5f6b3a)}
.about-photo{position:absolute;left:59px;top:28px;width:168px;height:168px;border-radius:50%;background:radial-gradient(circle at 50% 45%,#e8ecef,#b8c7d4 60%,#8fa3b6)}
.about-body{position:absolute;left:256px;top:42px;width:356px;color:var(--paper)}
.about-body h2{font-family:"Lora",serif;font-weight:700;font-size:20px;margin-bottom:9px}
.about-body p{font-size:7.4px;line-height:13.4px}
.btn-outline{display:inline-block;margin-top:15px;width:94px;height:28px;border:1.5px solid var(--paper);border-radius:3px;color:var(--paper);font-family:"Lora",serif;font-weight:700;font-size:8px;text-align:center;line-height:25px}

/* Panels */
.panels{position:absolute;top:553px;left:0;width:667px;height:295px;background:linear-gradient(160deg,#323d22,#29321b 50%,#343f24)}
.panel{position:absolute;top:43px;width:168px;height:209px;background:var(--paper);border:2px solid var(--olive);overflow:hidden}
.panel h3{height:39px;background:var(--olive);color:var(--paper);font-family:"Lora",serif;font-size:15px;font-weight:400;text-align:center;line-height:39px;margin:-2px -2px 0}
.panel.quick{left:55px}.panel.what{left:250px}.panel.blog{left:444px}
.quick-list{list-style:none;padding:8px 5px 0}
.quick-list li{display:flex;align-items:center;gap:10px;height:35px;border-bottom:1px solid #ddd;padding-left:6px;font-family:"Lora",serif;font-weight:700;font-size:9.5px}
.quick-list li:last-child{border-bottom:none}
.quick-list svg{width:22px;height:22px;fill:var(--olive)}
.what-list{list-style:none;padding:13px 4px 0 8px}
.what-list li{display:flex;align-items:center;gap:6px;font-size:6.7px;line-height:11.5px;margin-bottom:9px;white-space:nowrap}
.what-list svg{flex:none;width:17px;height:17px;fill:var(--olive)}
.blog-list{list-style:none;padding:14px 6px 0 10px}
.blog-list li{display:flex;gap:6px;font-size:6.7px;line-height:12px;margin-bottom:8.5px;white-space:nowrap}
.blog-list li::before{content:"\2192";color:var(--olive);font-size:8px}
.more-link{position:absolute;right:10px;bottom:11px;font-family:"Lora",serif;font-weight:700;font-size:7.5px;color:var(--accent-red)}

/* Newsletter */
.newsletter{position:absolute;top:848px;left:0;width:667px;height:156px;background:linear-gradient(120deg,#7c8753,#66723e 35%,#7a8551 60%,#5e6a37)}
.newsletter h2{position:absolute;top:46px;width:100%;text-align:center;font-family:"Lora",serif;font-weight:700;font-size:19.5px;color:var(--paper)}
.field{position:absolute;top:91px;width:168px;height:21px;background:var(--paper);font-size:6.5px;color:#444;padding-left:9px;line-height:21px}
.field.name{left:108px}.field.email{left:290px}
.btn-submit{position:absolute;top:91px;left:475px;width:70px;height:21px;border:1.5px solid var(--paper);border-radius:3px;color:var(--paper);font-family:"Lora",serif;font-weight:700;font-size:7.5px;text-align:center;line-height:18px}

/* Footer */
.site-footer{position:absolute;top:1004px;left:0;width:667px;height:160px;background:var(--footer);color:var(--paper)}
.site-footer h4{font-family:"Lora",serif;font-weight:700;font-size:10px;margin-bottom:11px}
.site-footer ul{list-style:none;font-size:7px;line-height:13.4px}
.f-about{position:absolute;left:57px;top:32px;width:185px}
.f-about p{font-size:7px;line-height:13px}
.socials{display:flex;gap:4px;margin-top:12px}
.socials span{width:26px;height:26px;border-radius:4px;background:#555}
.f-links{position:absolute;left:297px;top:32px}
.f-res{position:absolute;left:416px;top:32px}
.f-contact{position:absolute;left:521px;top:32px}
.f-contact li{display:flex;align-items:center;gap:6px}
.f-contact svg{width:7px;height:7px;fill:var(--paper)}
.footer-bottom{position:absolute;top:1164px;left:0;width:667px;height:36px;background:var(--footer-bottom);color:var(--paper);font-size:7px;text-align:center;line-height:36px}
</style>
</head>
<body>

<header class="site-header">
  <div class="brand">HARBORWELL</div>
  <div class="header-actions">
    <span class="btn-sm outline">Join Us</span>
    <span class="btn-sm">Signup</span>
    <span class="btn-sm">Veterans Signup</span>
  </div>
  <nav class="main-nav">
    <span class="active">Home</span><span>About Us</span><span>Membership</span><span>Research</span><span>Conferences</span><span>News</span><span>Contact</span>
  </nav>
</header>

<section class="hero">
  <div class="hero-photo" role="img" aria-label="Photo of a doctor in a white coat talking with a uniformed service member in a bright room"></div>
  <h1 class="hero-title">Harborwell</h1>
  <p class="hero-sub">Praesent Ac Purus Turpis. Curabitur Congue Ex Sem Sit Amet</p>
  <span class="btn-donate">DONATE</span>
  <div class="hero-dots"><span class="on"></span><span></span><span></span><span></span></div>
</section>

<section class="about">
  <div class="about-photo" role="img" aria-label="Photo of a team of medical providers gathered around a laptop"></div>
  <div class="about-body">
    <h2>About Us</h2>
    <p>Vestibulum lectus nibh, consectetur nec nunc non, scelerisque vulputate nunc. Praesent ac purus turpis. Curabitur congue ex sem, sit amet scelerisque nisi convallis non. Vivamus rutrum imperdiet sodales. Vivamus ante sapien, laoreet at elementum id, suscipit vitae augue. Phasellus eget leo an, tristique orci sed, elementum lectus. Phasellused dui posuere semper.</p>
    <span class="btn-outline">READ MORE</span>
  </div>
</section>

<section class="panels">
  <div class="panel quick">
    <h3>QUICK LINKS</h3>
    <ul class="quick-list">
      <li><svg viewBox="0 0 24 24"><path d="M2 10h10V5l8 7-8 7v-5H2z"/><path d="M17 3h5v18h-5v-2h3V5h-3z"/></svg>Sign Up For Membership</li>
      <li><svg viewBox="0 0 24 24"><circle cx="12" cy="7" r="5"/><path d="M3 22c0-6 4-9 9-9s9 3 9 9z"/></svg>Join Us</li>
      <li><svg viewBox="0 0 24 24"><rect x="3" y="5" width="14" height="9" rx="2" transform="rotate(25 10 10)"/><circle cx="16" cy="17" r="5"/></svg>Donate Us</li>
      <li><svg viewBox="0 0 24 24"><circle cx="9" cy="6" r="4"/><path d="M1 20c0-5 3-8 8-8s7 2 7 5H1z"/><path d="M18 12l1.5 3 3.3.4-2.4 2.3.6 3.3-3-1.6-3 1.6.6-3.3-2.4-2.3 3.3-.4z"/></svg>Veterans Sign Up</li>
    </ul>
  </div>

  <div class="panel what">
    <h3>WHAT WE DO</h3>
    <ul class="what-list">
      <li><svg viewBox="0 0 24 24"><path d="M5 2v7a5 5 0 0010 0V2h-2v7a3 3 0 01-6 0V2z"/><path d="M9 14h2v3a4 4 0 008 0v-3h2v3a6 6 0 01-12 0z"/><circle cx="20" cy="12" r="2"/></svg><span>Vivamus ante sapien, laore;o hjkuet at<br>elementum id, suscipit vitae augue.</span></li>
      <li><svg viewBox="0 0 24 24"><ellipse cx="11" cy="14" rx="9" ry="7"/><circle cx="16" cy="6" r="3"/></svg><span>Vivamus ante sapien, laore;o hjkuet at<br>elementum id, suscipit vitae augue.</span></li>
      <li><svg viewBox="0 0 24 24"><circle cx="12" cy="5" r="3"/><path d="M2 16h5l4 3h7l4-4v4l-4 4H2z"/><rect x="9" y="9" width="6" height="6"/></svg><span>Vivamus ante sapien, laore;o hjkuet at<br>elementum id, suscipit vitae augue.</span></li>
      <li><svg viewBox="0 0 24 24"><rect x="2" y="14" width="4" height="8"/><rect x="8" y="10" width="4" height="12"/><rect x="14" y="12" width="4" height="10"/><path d="M2 10l6-5 5 3 7-6v3l-7 6-5-3-6 5z"/></svg><span>Vivamus ante sapien, laore;o hjkuet at<br>elementum id, suscipit vitae augue.</span></li>
    </ul>
    <span class="more-link">READ MORE...</span>
  </div>

  <div class="panel blog">
    <h3>BLOG</h3>
    <ul class="blog-list">
      <li><span>Vestibulum lectus nibh, consectetur nec<br>non, scelerisque vulputate nunc.</span></li>
      <li><span>Vestibulum lectus nibh, consectetur nec<br>non, scelerisque vulputate nunc.</span></li>
      <li><span>Vestibulum lectus nibh, consectetur nec<br>non, scelerisque vulputate nunc.</span></li>
      <li><span>Vestibulum lectus nibh, consectetur nec<br>non, scelerisque vulputate nunc.</span></li>
    </ul>
    <span class="more-link">VIEW ALL &#10230;</span>
  </div>
</section>

<section class="newsletter" role="img" aria-label="Olive camouflage texture background">
  <h2>NEWSLETTER SUBSCRIPTION</h2>
  <div class="field name">NAME</div>
  <div class="field email">EMAIL</div>
  <span class="btn-submit">SUBMIT</span>
</section>

<footer class="site-footer">
  <div class="f-about">
    <h4>Harborwell</h4>
    <p>Praesent vitae dui mauris. Suspendisse massa odio, suscipit quis euismod finibus, viverra in est. Nullam sollicitudin vulputate dololus aliquet nec.</p>
    <div class="socials"><span></span><span></span><span></span></div>
  </div>
  <div class="f-links">
    <h4>Quick Links</h4>
    <ul><li>Home</li><li>About Us</li><li>Membership</li><li>Research</li><li>Conferences</li><li>News</li><li>Contact</li></ul>
  </div>
  <div class="f-res">
    <h4>Resources</h4>
    <ul><li>Terms of Use</li><li>Privacy Policy</li><li>Disclaimer</li></ul>
  </div>
  <div class="f-contact">
    <h4>Contact Us</h4>
    <ul>
      <li><svg viewBox="0 0 24 24"><path d="M6 2l4 5-2 3c1 3 3 5 6 6l3-2 5 4-3 4C10 22 2 14 2 5z"/></svg>+1 555 010 0199</li>
      <li><svg viewBox="0 0 24 24"><path d="M2 5h20v14H2zm2 2v1l8 5 8-5V7l-8 5z"/></svg>info@harborwellnet.org</li>
    </ul>
  </div>
</footer>
<div class="footer-bottom">Copyright © 2018. All Rights Reserved.</div>

</body>
</html>
```